Business Card Design for Occupational Medicine Start Up Company

We need to design a professional business card. We are a healthcare company providing occupational medicine services to blue collar industries. We are professional, efficient and high quality service providers.

Target Market(s)

Blue Collar Industry: Shipbuilding, Ports, Trucking Companies; The Executives and Safety Officers for these companies

Industry/Entity Type

Healthcare

Contact Information for Business Card

Logo, Name, Title, Email, Phone

Other font styles liked:
• Please match our Brand Guide

Requirements
Must have
• Our Company Colors and Logo

```html
<!DOCTYPE html>
<html lang="en">
<head>
<meta charset="UTF-8">
<title>Crewline Clinics – Business Card</title>
<link href="https://fonts.googleapis.com/css2?family=Montserrat:wght@400;600;700;800&family=Poppins:wght@400;600;700&display=swap" rel="stylesheet">
<style>
  :root {
    --navy: #2b2f7e;
    --sky: #22a6df;
    --sky-soft: #2ba9e1;
    --amber: #f4ae3f;
    --ink: #141414;
    --paper: #ffffff;
    --page: #ffffff;
    --mist: #eef0f7;
  }
  * { box-sizing: border-box; margin: 0; padding: 0; }
  html, body { width: 670px; height: 1200px; overflow: hidden; background: var(--page); }
  body { font-family: "Montserrat", sans-serif; position: relative; }

  .card {
    position: absolute;
    left: 55px;
    width: 560px;
    height: 320px;
    overflow: hidden;
    box-shadow: 0 6px 10px rgba(0,0,0,0.18);
  }
  .card--front { top: 250px; background: var(--paper); }
  .card--back { top: 630px; background: var(--sky); }

  /* front */
  .front__texture {
    position: absolute; inset: 0 0 72px 0;
    background: radial-gradient(ellipse at center, var(--paper) 35%, var(--mist) 100%);
  }
  .front__rule {
    position: absolute; left: 0; right: 0; top: 249px; height: 7px; background: var(--amber);
  }
  .front__band {
    position: absolute; left: 0; right: 0; top: 256px; bottom: 0; background: var(--sky);
    display: flex; align-items: center; justify-content: center;
  }
  .front__web {
    font-weight: 800; font-size: 17px; letter-spacing: 4.2px; color: var(--paper);
  }
  .front__web .dim { color: var(--ink); }

  .brand {
    position: absolute; display: flex; flex-direction: column; align-items: center;
    font-family: "Montserrat", sans-serif; font-weight: 700; text-align: center;
  }
  .brand__dot { border-radius: 50%; margin-bottom: 14px; }
  .brand__name { line-height: 1; letter-spacing: 1px; }
  .brand__sub { line-height: 1; margin-top: 8px; }

  .card--front .brand { left: 0; right: 0; top: 66px; color: var(--navy); }
  .card--front .brand__dot { width: 56px; height: 56px; background: var(--navy); }
  .card--front .brand__name { font-size: 34px; }
  .card--front .brand__sub { font-size: 18px; letter-spacing: 9px; padding-left: 9px; }

  /* back */
  .back__texture {
    position: absolute; left: 0; right: 0; height: 68px;
    background: linear-gradient(180deg, rgba(20,140,200,0.35), rgba(34,166,223,0));
  }
  .back__texture--top { top: 0; }
  .back__texture--bottom { bottom: 0; transform: scaleY(-1); }

  .contact {
    position: absolute; left: 0; top: 67px; width: 271px; height: 181px;
    background: var(--paper); border-radius: 0 18px 18px 0;
    padding: 14px 0 0 32px; font-family: "Poppins", sans-serif;
  }
  .contact__name {
    display: inline-block; font-size: 24px; line-height: 1.15; color: var(--ink); font-weight: 400;
    border-bottom: 1.5px solid var(--amber); padding-bottom: 1px;
  }
  .contact__name strong { color: var(--sky); font-weight: 700; }
  .contact__title { font-size: 16px; font-weight: 700; color: var(--sky); margin-top: 2px; }
  .contact__list { list-style: none; margin-top: 10px; }
  .contact__item {
    display: flex; align-items: center; gap: 10px; height: 32px;
    font-size: 12.5px; color: var(--ink);
  }
  .contact__icon { width: 19px; height: 22px; flex: none; }

  .card--back .brand { left: 304px; width: 220px; top: 82px; color: var(--paper); }
  .card--back .brand__dot { width: 52px; height: 52px; background: var(--paper); }
  .card--back .brand__name { font-size: 26px; }
  .card--back .brand__sub { font-size: 15px; letter-spacing: 7px; padding-left: 7px; }
</style>
</head>
<body>

<section class="card card--front" aria-label="Business card front">
  <div class="front__texture" role="img" aria-label="Faint hexagon and medical cross pattern"></div>
  <div class="brand">
    <span class="brand__dot"></span>
    <span class="brand__name">CREWLINE</span>
    <span class="brand__sub">CLINICS</span>
  </div>
  <div class="front__rule"></div>
  <div class="front__band">
    <p class="front__web"><span class="dim">www.</span>crewlineclinics<span class="dim">.com</span></p>
  </div>
</section>

<section class="card card--back" aria-label="Business card back">
  <div class="back__texture back__texture--top" role="img" aria-label="Faint hexagon and medical cross pattern"></div>
  <div class="back__texture back__texture--bottom" role="img" aria-label="Faint hexagon and medical cross pattern"></div>

  <div class="contact">
    <h1 class="contact__name">Dana <strong>Whitfield</strong></h1>
    <p class="contact__title">Executive Officer</p>
    <ul class="contact__list">
      <li class="contact__item">
        <svg class="contact__icon" viewBox="0 0 19 22" aria-hidden="true">
          <rect x="0.5" y="1.5" width="18" height="19" fill="#fff" stroke="#22a6df"/>
          <rect x="0.5" y="17" width="18" height="3.5" fill="#f4ae3f"/>
          <path d="M6 5c-1 1-1 3 1 6s4 4 5 4l1.5-1.5-2-2-1 .8c-1-.5-2-1.8-2.4-2.8l.8-1-2-2z" fill="#2b2f7e"/>
        </svg>
        (555) 012-3456
      </li>
      <li class="contact__item">
        <svg class="contact__icon" viewBox="0 0 19 22" aria-hidden="true">
          <rect x="0.5" y="1.5" width="18" height="19" fill="#fff" stroke="#22a6df"/>
          <rect x="0.5" y="17" width="18" height="3.5" fill="#f4ae3f"/>
          <rect x="3.5" y="6" width="12" height="8" fill="#2b2f7e"/>
          <path d="M3.5 6l6 4.5 6-4.5" fill="none" stroke="#fff" stroke-width="1"/>
        </svg>
        d.whitfield@crewline.com
      </li>
      <li class="contact__item">
        <svg class="contact__icon" viewBox="0 0 19 22" aria-hidden="true">
          <rect x="0.5" y="1.5" width="18" height="19" fill="#fff" stroke="#22a6df"/>
          <rect x="0.5" y="17" width="18" height="3.5" fill="#f4ae3f"/>
          <circle cx="9.5" cy="10" r="5.2" fill="#2b2f7e"/>
          <path d="M4.3 10h10.4M9.5 4.8v10.4M6.5 6.5q3 3.5 0 7M12.5 6.5q-3 3.5 0 7" fill="none" stroke="#fff" stroke-width="0.7"/>
        </svg>
        www.crewlineclinics.com
      </li>
    </ul>
  </div>

  <div class="brand">
    <span class="brand__dot"></span>
    <span class="brand__name">CREWLINE</span>
    <span class="brand__sub">CLINICS</span>
  </div>
</section>

</body>
</html>
```